Business Card Design

Business Card for professional consulting firm working with large financial institutions.

Target Market(s)

Executive buyers

Industry/Entity Type

Banking

Contact Information for Business Card

Mild creativity wanted. Not boring, but do elaborate artwork.

Font styles to use
Serif
Sans Serif

Colors

Designer to choose colors to be used in the design.

Requirements
Must have
• Standard business card features - company name, individual name, telephone, website, email, locations.
Nice to have
• Two colors
Should not have
• too many colors, fancy printing, cartoons.

```html
<!DOCTYPE html>
<html lang="en">
<head>
<meta charset="utf-8">
<title>Corvanta Business Card</title>
<link href="https://fonts.googleapis.com/css2?family=Lora:wght@400&family=Montserrat:wght@400;500;700&display=swap" rel="stylesheet">
<style>
  :root {
    --backdrop: #2b2e33;
    --ink: #1f1f1f;
    --paper: #ffffff;
    --silver: #c6c6c6;
    --mark-grey: #4d4d4d;
    --text-light: #ffffff;
    --text-muted: #d2d2d2;
  }
  * { margin: 0; padding: 0; box-sizing: border-box; }
  html, body { width: 1200px; height: 1054px; overflow: hidden; }
  body {
    background: var(--backdrop);
    font-family: "Montserrat", sans-serif;
    position: relative;
  }
  .card {
    position: absolute;
    left: 190px;
    width: 820px;
    height: 469px;
    border-radius: 34px;
    overflow: hidden;
    box-shadow: 0 14px 30px rgba(0,0,0,0.45);
  }
  .card--front { top: 40px; background: var(--paper); }
  .card--back { top: 545px; background: var(--ink); }
  .card__shape { position: absolute; inset: 0; }
  .brand-name {
    position: absolute;
    font-family: "Lora", serif;
    font-weight: 400;
    letter-spacing: 1px;
  }
  .card--front .brand-name {
    left: 40px; top: 190px; width: 360px;
    text-align: center;
    font-size: 50px;
    color: var(--mark-grey);
  }
  .card--back .brand-name {
    left: 0; right: 0; top: 180px;
    text-align: center;
    font-size: 78px;
    color: var(--text-light);
  }
  .contact-block {
    position: absolute;
    left: 520px; top: 110px;
    color: var(--text-light);
  }
  .person-name { font-size: 34px; font-weight: 700; letter-spacing: 0.5px; }
  .person-title { font-size: 17px; color: var(--text-muted); margin-top: 4px; }
  .divider { width: 44px; height: 2px; background: var(--text-muted); margin: 24px 0 26px; }
  .address { font-size: 17px; line-height: 1.45; color: var(--text-muted); margin-bottom: 18px; }
  .contact-line {
    display: flex; align-items: center; gap: 12px;
    font-size: 17px; color: var(--text-muted); margin-bottom: 8px;
  }
  .contact-line svg { width: 18px; height: 18px; flex: none; }
</style>
</head>
<body>
  <section class="card card--front">
    <svg class="card__shape" viewBox="0 0 820 469" aria-hidden="true">
      <path d="M470 0 Q458 300 262 469 L820 469 L820 0 Z" fill="var(--silver)"/>
      <path d="M492 0 Q482 305 290 469 L820 469 L820 0 Z" fill="var(--ink)"/>
    </svg>
    <div class="brand-name">corvanta</div>
    <div class="contact-block">
      <div class="person-name">Daniel HOLT</div>
      <div class="person-title">Managing Director</div>
      <div class="divider"></div>
      <div class="address">418 N Harbor Avenue 2210<br>Lakeview Hollow, MS 39017</div>
      <div class="contact-line">
        <svg viewBox="0 0 24 24"><path d="M6.6 10.8a15 15 0 0 0 6.6 6.6l2.2-2.2a1 1 0 0 1 1-.25 11 11 0 0 0 3.6.6 1 1 0 0 1 1 1V20a1 1 0 0 1-1 1A17 17 0 0 1 3 4a1 1 0 0 1 1-1h3.5a1 1 0 0 1 1 1c0 1.25.2 2.45.6 3.6a1 1 0 0 1-.25 1z" fill="currentColor"/></svg>
        000.000.0000
      </div>
      <div class="contact-line">
        <svg viewBox="0 0 24 24"><rect x="3" y="5" width="18" height="14" rx="1" fill="none" stroke="currentColor" stroke-width="2"/><path d="M3 6l9 7 9-7" fill="none" stroke="currentColor" stroke-width="2"/></svg>
        daniel@corvanta.com
      </div>
      <div class="contact-line">
        <svg viewBox="0 0 24 24"><circle cx="12" cy="12" r="9" fill="none" stroke="currentColor" stroke-width="2"/><path d="M3 12h18M12 3c3 3 3 15 0 18M12 3c-3 3-3 15 0 18" fill="none" stroke="currentColor" stroke-width="1.6"/></svg>
        www.corvanta.com
      </div>
    </div>
  </section>

  <section class="card card--back">
    <div class="brand-name">corvanta</div>
  </section>
</body>
</html>
```